Quiet Harbor Prints gallery website

I need a Website for a gallery with a shopify integration or maybe even better also compatible with squarespace.
the website should have following riders: Künstler, Veranstaltungen, Shop, About Us.
some nice examples for inspiration of the website architecture are:
https://www.lindwerkraum.com/
https://www.plattenbau-salon.com/de/
https://moorlichtraum.de/
It should be easy for us to make adaptations and fill the website with new content.
Attached there is the CI an logo for the brand.
Target Market(s)
Art Collectors,
Industry/Entity Type
artgallery
Coding
Coded - Design and coding required
Number of Pages Required
3 page
Font styles to use
Look and feel

```html
<!DOCTYPE html>
<html lang="en">
<head>
<meta charset="utf-8">
<title>Quiet Harbor Prints — Hamburg</title>
<link href="https://fonts.googleapis.com/css2?family=Montserrat:wght@300;400;500;600;700&display=swap" rel="stylesheet">
<style>
:root{
  --red:#c0222d;
  --ink:#1d1d1d;
  --muted:#444;
  --line:#cfcfcf;
  --tile:#efefef;
  --band:#f3f3f3;
  --blush:#fde8ea;
  --night:#0d1430;
  --footer:#232323;
  --white:#fff;
}
*{box-sizing:border-box;margin:0;padding:0}
html,body{width:1200px;height:4357px;overflow:hidden}
body{font-family:"Montserrat",sans-serif;color:var(--ink);background:var(--white);position:relative}
.abs{position:absolute}
a{color:inherit;text-decoration:none}
.btn{position:absolute;background:var(--red);color:var(--white);font-weight:700;font-size:14px;display:flex;align-items:center;justify-content:center;letter-spacing:.3px}
.heading{position:absolute;font-weight:700;font-size:28px;text-transform:uppercase;letter-spacing:.3px}
.rule{position:absolute;height:3px;width:54px;background:var(--red)}
.body-text{position:absolute;font-size:14px;line-height:27px;color:var(--muted)}
.icon-circle{position:absolute;width:40px;height:40px;border-radius:50%;background:var(--red);display:flex;align-items:center;justify-content:center}
.ph{position:absolute}
/* wordmark: one colour, one weight, one plain square beside */
.wordmark{position:absolute;display:flex;align-items:center;gap:10px;white-space:nowrap;font-weight:600}
.wordmark-square{width:12px;height:12px;background:var(--red);flex:none}
.contact-label{font-weight:600;font-size:15px}
.contact-value{font-size:11px;color:var(--muted);margin-top:6px}
.nav{position:absolute;left:441px;top:99px;display:flex;gap:22px;font-size:14px;color:var(--muted)}
.search{position:absolute;left:867px;top:93px;width:230px;height:34px;border-radius:17px;background:var(--tile);display:flex;align-items:center;padding-left:14px;font-size:16px;font-weight:500;gap:5px}
.tab{position:absolute;top:1417px;height:42px;display:flex;align-items:center;justify-content:center;font-size:13px;font-weight:700;border:2px solid var(--red)}
.product{position:absolute;top:1503px;width:208px;text-align:center}
.product-frame{height:244px;background:var(--tile);display:flex;align-items:center;justify-content:center}
.product-name{font-weight:700;font-size:17px;margin-top:17px}
.product-price{font-weight:700;font-size:18px;color:var(--red);margin-top:12px}
.edition{position:absolute;top:2166px;width:320px;height:351px;background:var(--white);border:1px solid #e2e2e2;padding:10px}
.edition-label{font-weight:700;font-size:24px;margin-top:18px;padding-left:5px}
.event{position:absolute;top:2717px;width:335px;height:358px;background:var(--white);box-shadow:0 0 0 1px #ececec}
.event-date{position:absolute;right:23px;top:-17px;width:66px;height:76px;background:var(--red);color:var(--white);font-weight:700;font-size:18px;text-align:center;line-height:24px;padding-top:14px}
.event-label{position:absolute;left:0;right:0;bottom:0;height:78px;display:flex;align-items:center;justify-content:space-between;padding:0 22px;font-weight:600;font-size:17px;background:#f6f6f6}
.event-label span:last-child{color:var(--red);font-size:26px;font-weight:500}
.footer{position:absolute;left:0;top:4059px;width:1200px;height:298px;background:var(--footer);color:var(--white)}
.footer-links{position:absolute;left:479px;top:68px;display:flex;gap:22px;font-size:14px}
.f-contact{position:absolute;top:144px;display:flex;gap:12px}
.f-contact b{font-size:15px;display:block;white-space:nowrap}
.f-contact small{font-size:11px;display:block;margin-top:4px;line-height:15px;white-space:nowrap}
.pay{display:inline-block;width:38px;height:24px;border-radius:3px;background:var(--white);margin-left:13px}
</style>
</head>
<body>

<header>
  <div class="wordmark" style="left:112px;top:88px;font-size:16px;color:var(--ink)">
    <span class="wordmark-square"></span><span>Quiet Harbor Prints</span>
  </div>
  <div class="icon-circle" style="left:437px;top:22px">
    <svg width="18" height="18" viewBox="0 0 24 24"><path fill="#fff" d="M6.6 10.8a15 15 0 0 0 6.6 6.6l2.2-2.2a1 1 0 0 1 1-.25 11.4 11.4 0 0 0 3.6.57 1 1 0 0 1 1 1V20a1 1 0 0 1-1 1A17 17 0 0 1 3 4a1 1 0 0 1 1-1h3.5a1 1 0 0 1 1 1c0 1.25.2 2.45.57 3.57a1 1 0 0 1-.25 1z"/></svg>
  </div>
  <div class="abs" style="left:492px;top:20px"><div class="contact-label">Phone Number :</div><div class="contact-value">+1 555 014 2290</div></div>
  <div class="icon-circle" style="left:653px;top:22px">
    <svg width="18" height="18" viewBox="0 0 24 24"><path fill="#fff" d="M3 6h18v1.5l-9 5.5-9-5.5zM3 9.5l9 5.5 9-5.5V18H3z"/></svg>
  </div>
  <div class="abs" style="left:707px;top:20px"><div class="contact-label">Email :</div><div class="contact-value">info@qhprints.example</div></div>
  <svg class="abs" style="left:921px;top:22px" width="34" height="34" viewBox="0 0 34 34" role="img" aria-label="German language flag"><clipPath id="fc"><circle cx="17" cy="17" r="16"/></clipPath><g clip-path="url(#fc)"><rect width="34" height="11.4" fill="#111"/><rect y="11.3" width="34" height="11.4" fill="#dd0000"/><rect y="22.6" width="34" height="11.4" fill="#ffce00"/></g></svg>
  <div class="abs" style="left:967px;top:29px;font-weight:700;font-size:15px">En ⌄</div>
  <svg class="abs" style="left:1038px;top:30px" width="16" height="18" viewBox="0 0 16 18"><circle cx="8" cy="5" r="4" fill="#ccc"/><path d="M0 18c0-5 3.5-7 8-7s8 2 8 7z" fill="#ccc"/></svg>
  <svg class="abs" style="left:1062px;top:30px" width="22" height="19" viewBox="0 0 24 21"><path fill="#ccc" d="M12 21 2 11A6 6 0 0 1 12 3a6 6 0 0 1 10 8z"/></svg>
  <div class="abs" style="left:438px;top:79px;width:665px;height:2px;background:var(--line)"></div>
  <div class="abs" style="left:438px;top:78px;width:42px;height:3px;background:var(--red)"></div>
  <nav class="nav"><a>Home</a><a>Artists</a><a>Events</a><a>Shop</a><a>About Us</a></nav>
  <div class="search"><svg width="15" height="15" viewBox="0 0 16 16"><circle cx="6.5" cy="6.5" r="5" fill="none" stroke="#111" stroke-width="2.2"/><path d="M10 10l5 5" stroke="#111" stroke-width="2.4"/></svg>Search</div>
</header>

<section class="hero abs" style="left:0;top:142px;width:1200px;height:599px;background:var(--night)">
  <div class="ph" role="img" aria-label="Hero photograph: model in vivid body paint pointing left" style="left:560px;top:0;width:640px;height:599px;background:radial-gradient(ellipse at 65% 55%,#c8402a 0%,#7a2a5a 35%,#1a1d45 70%,var(--night) 100%)"></div>
  <div class="abs" style="left:105px;top:156px;color:var(--white);font-size:40px;font-weight:400;letter-spacing:.5px;white-space:nowrap">QUIET HARBOR PRINTS</div>
  <div class="abs" style="left:105px;top:210px;color:var(--white);font-size:38px;font-weight:700;letter-spacing:1px">HANBURG</div>
  <p class="abs" style="left:105px;top:278px;width:440px;color:var(--white);font-size:14px;line-height:29px">Lorem ipsum dolor sit amet, consectetur adipiscing elit, sed do eiusmod tempor incididunt ut labore et dolore magna aliqua.</p>
  <a class="btn" style="left:105px;top:384px;width:132px;height:46px">SHOP NOW</a>
  <svg class="abs" style="left:104px;top:480px" width="42" height="18" viewBox="0 0 42 18"><circle cx="8" cy="9" r="8" fill="#fff"/><path d="M12 9H5m3-3-3 3 3 3" stroke="#0d1430" stroke-width="2" fill="none"/><circle cx="32" cy="9" r="8" fill="#fff"/><path d="M28 9h7m-3-3 3 3-3 3" stroke="#0d1430" stroke-width="2" fill="none"/></svg>
</section>

<section class="about">
  <div class="wordmark" style="left:222px;top:996px;font-size:20px;color:var(--red)">
    <span class="wordmark-square" style="width:16px;height:16px"></span><span>Quiet Harbor Prints</span>
  </div>
  <h2 class="heading" style="left:557px;top:832px">About Us</h2>
  <div class="rule" style="left:557px;top:870px"></div>
  <p class="body-text" style="left:557px;top:888px;width:495px">Lorem ipsum dolor sit amet, consectetur adipiscing elit, sed do eiusmod tempor incididunt ut labore et dolore magna aliqua. Quis ipsum suspendisse ultrices gravida.</p>
  <p class="body-text" style="left:557px;top:978px;width:495px">Sed ut perspiciatis unde omnis iste natus error sit voluptatem accusantium doloremque laudantium, totam rem aperiam, eaque ipsa quae ab illo inventore veritatis et quasi architecto beatae vitae dicta sunt explicabo. Nemo enim ipsam voluptatem quia voluptas sit aspernatur aut odit aut fugit.</p>
  <a class="btn" style="left:557px;top:1131px;width:134px;height:46px">READ MORE</a>
  <div class="abs" style="left:105px;top:1274px;width:992px;height:1px;background:var(--line)"></div>
</section>

<section class="products">
  <h2 class="heading" style="left:0;width:1200px;text-align:center;top:1332px">Our Products</h2>
  <div class="rule" style="left:573px;top:1370px"></div>
  <div class="tab" style="left:452px;width:136px;background:var(--red);color:var(--white)">FEATURED</div>
  <div class="tab" style="left:587px;width:159px;color:var(--ink)">MOST POPULAR</div>
  <div class="product" style="left:117px"><div class="product-frame"><div role="img" aria-label="Framed portrait print with gold patterned headwrap" style="width:152px;height:188px;border:5px solid #222;background:linear-gradient(160deg,#2b5a66,#7a4a22 55%,#1a1a1a)"></div></div><div class="product-name">Product Name</div><div class="product-price">$52.00</div></div>
  <div class="product" style="left:374px"><div class="product-frame"><div role="img" aria-label="Framed abstract print in turquoise and magenta" style="width:146px;height:140px;border:5px solid #222;background:linear-gradient(135deg,#2fa7c9,#e27a3a 50%,#b62a8a)"></div></div><div class="product-name">Product Name</div><div class="product-price">$22.00</div></div>
  <div class="product" style="left:630px"><div class="product-frame"><div role="img" aria-label="Framed floral collage print" style="width:104px;height:128px;border:5px solid #222;background:linear-gradient(180deg,#cfd8d8,#7e98a8 60%,#405060)"></div></div><div class="product-name">Product Name</div><div class="product-price">$50.00</div></div>
  <div class="product" style="left:887px"><div class="product-frame"><div role="img" aria-label="Framed swirling night landscape print" style="width:146px;height:58px;border:3px solid #222;background:linear-gradient(180deg,#1f3f8a,#e09a2a 55%,#1b3040)"></div></div><div class="product-name">Product Name</div><div class="product-price">$80.00</div></div>
  <a class="btn" style="left:533px;top:1855px;width:135px;height:47px">VIEW MORE</a>
</section>

<section class="editions abs" style="left:0;top:1995px;width:1200px;height:642px;background:var(--band)">
  <h2 class="heading" style="left:0;width:1200px;text-align:center;top:72px">Arts Editions</h2>
  <div class="rule" style="left:573px;top:110px"></div>
</section>
<div class="edition" style="left:103px"><div role="img" aria-label="Artwork: flaming apple on dark background" style="height:274px;background:radial-gradient(circle at 50% 55%,#e8442a,#f0a22a 35%,#1c2a3a 75%)"></div><div class="edition-label">Lorem Ipsum</div></div>
<div class="edition" style="left:440px"><div role="img" aria-label="Artwork: misty ink-wash mountain landscape" style="height:274px;background:linear-gradient(180deg,#b9cbd8,#8fa7a8 50%,#5c6b55)"></div><div class="edition-label">Lorem Ipsum</div></div>
<div class="edition" style="left:777px"><div role="img" aria-label="Artwork: bison standing before a sunset" style="height:274px;background:linear-gradient(180deg,#2a7a9a,#e0902a 50%,#4a2a1a)"></div><div class="edition-label">Lorem Ipsum</div></div>

<section class="events">
  <div class="event" style="left:103px"><div role="img" aria-label="Photo: visitors in a gallery hall" style="height:280px;background:linear-gradient(180deg,#6b5a46,#a08462 55%,#3a2a1e)"></div><div class="event-date">FEB<br>25</div><div class="event-label"><span>Event Name : Lorem Ipsum</span><span>+</span></div></div>
  <div class="event" style="left:457px"><div role="img" aria-label="Photo: painter working at an outdoor table" style="height:280px;background:linear-gradient(160deg,#8a9a9a,#7a5a3a 50%,#3a4a6a)"></div><div class="event-date">FEB<br>28</div><div class="event-label"><span>Event Name : Lorem Ipsum</span><span>+</span></div></div>
  <h2 class="heading" style="right:103px;top:2763px">Events</h2>
  <div class="rule" style="left:1043px;top:2802px"></div>
  <p class="body-text" style="right:103px;top:2818px;width:280px;text-align:right;font-size:13px;line-height:23px">Lorem ipsum dolor sit amet, consectetur adipiscing elit, sed do eiusmod tempor incididunt ut labore et dolore magna aliqua.</p>
</section>

<section class="work">
  <div class="abs" style="left:0;top:3250px;width:562px;height:341px;background:var(--blush)"></div>
  <div class="abs" style="left:0;top:3591px;width:1200px;height:31px;background:var(--blush)"></div>
  <div class="abs" style="left:164px;top:3294px;width:398px;height:6px;background:var(--white)"></div>
  <div class="abs" style="left:0;top:3583px;width:338px;height:6px;background:var(--white)"></div>
  <h2 class="heading" style="left:105px;top:3352px">Our Work</h2>
  <div class="rule" style="left:105px;top:3390px"></div>
  <p class="body-text" style="left:105px;top:3430px;width:410px">Lorem ipsum dolor sit amet, consectetur adipiscing elit, sed do eiusmod tempor incididunt ut labore et dolore magna aliqua.</p>
  <div class="ph" role="img" aria-label="Artwork: colourful abstract crowd of figures" style="left:609px;top:3267px;width:193px;height:248px;background:linear-gradient(135deg,#2a4aa0,#e04a3a 45%,#f0c030 80%)"></div>
  <div class="ph" role="img" aria-label="Artwork: lion portrait in warm light" style="left:807px;top:3199px;width:168px;height:220px;background:linear-gradient(180deg,#3a2a1a,#c07a2a 55%,#5a3a1a)"></div>
  <div class="ph" role="img" aria-label="Artwork: abstract city in sunset tones" style="left:983px;top:3272px;width:112px;height:147px;background:linear-gradient(180deg,#3a4aa0,#e04a5a 60%,#f0a030)"></div>
  <div class="ph" role="img" aria-label="Artwork: painted portrait with vivid colour" style="left:809px;top:3424px;width:168px;height:215px;background:linear-gradient(160deg,#2a8aa0,#e0803a 50%,#8a2a6a)"></div>
  <div class="ph" role="img" aria-label="Artwork: figure in flowing red dress" style="left:983px;top:3427px;width:146px;height:164px;background:linear-gradient(180deg,#2a6a8a,#e06a2a 60%,#c0302a)"></div>
  <div class="ph" role="img" aria-label="Artwork: ornate golden abstract" style="left:689px;top:3524px;width:112px;height:145px;background:linear-gradient(160deg,#6a4a2a,#c09040 50%,#3a3a4a)"></div>
</section>

<section class="newsletter">
  <h2 class="heading" style="left:0;width:1200px;text-align:center;top:3761px">Subscribe to our Newsletter</h2>
  <div class="rule" style="left:573px;top:3803px"></div>
  <p class="body-text" style="left:260px;width:680px;text-align:center;top:3832px;font-size:14px;line-height:29px">With our newsletter you won't miss any exhibitions. You will also receive special offers and always receive the latest news.</p>
  <div class="abs" style="left:320px;top:3922px;width:560px;height:45px;border:1.5px solid var(--red);display:flex;align-items:center;padding-left:13px;font-size:14px">Enter Email</div>
  <div class="abs" style="left:821px;top:3922px;width:59px;height:45px;background:var(--red);display:flex;align-items:center;justify-content:center">
    <svg width="20" height="20" viewBox="0 0 24 24"><path fill="#fff" d="M22 2 2 10l7 3 9-8-7 9v7l4-5 4 3z"/></svg>
  </div>
</section>

<footer class="footer">
  <div class="wordmark" style="left:104px;top:186px;font-size:22px;color:var(--white)">
    <span class="wordmark-square" style="width:14px;height:14px;background:var(--white)"></span><span>Quiet Harbor Prints</span>
  </div>
  <nav class="footer-links"><a>Home</a><span>|</span><a>Artists</a><span>|</span><a>Events</a><span>|</span><a>Shop</a><span>|</span><a>About Us</a></nav>
  <div class="abs" style="left:472px;top:118px;width:625px;height:1px;background:#666"></div>
  <div class="f-contact" style="left:466px">
    <div class="icon-circle" style="position:static;flex:none"><svg width="14" height="18" viewBox="0 0 14 18"><path fill="#fff" d="M7 0a7 7 0 0 1 7 7c0 5-7 11-7 11S0 12 0 7a7 7 0 0 1 7-7z"/><circle cx="7" cy="7" r="2.5" fill="#c0222d"/></svg></div>
    <div><b>Location :</b><small>14 Dock Lane #5 Harborview,<br>TX 75000</small></div>
  </div>
  <div class="f-contact" style="left:693px">
    <div class="icon-circle" style="position:static;flex:none"><svg width="16" height="16" viewBox="0 0 24 24"><path fill="#fff" d="M6.6 10.8a15 15 0 0 0 6.6 6.6l2.2-2.2a1 1 0 0 1 1-.25 11.4 11.4 0 0 0 3.6.57 1 1 0 0 1 1 1V20a1 1 0 0 1-1 1A17 17 0 0 1 3 4a1 1 0 0 1 1-1h3.5a1 1 0 0 1 1 1c0 1.25.2 2.45.57 3.57a1 1 0 0 1-.25 1z"/></svg></div>
    <div><b>Phone Number :</b><small>+1 555 014 2290</small></div>
  </div>
  <div class="f-contact" style="left:906px">
    <div class="icon-circle" style="position:static;flex:none"><svg width="16" height="16" viewBox="0 0 24 24"><path fill="#fff" d="M3 6h18v1.5l-9 5.5-9-5.5zM3 9.5l9 5.5 9-5.5V18H3z"/></svg></div>
    <div><b>Email :</b><small>info@qhprints.example</small></div>
  </div>
  <div class="abs" style="left:484px;top:236px;font-size:11px">©Copyrights 2024 <span style="color:var(--red)">QUIET HARBOR PRINTS</span> | All Rights Reserved</div>
  <div class="abs" style="left:935px;top:227px"><span class="pay"></span><span class="pay"></span><span class="pay"></span></div>
</footer>

</body>
</html>
```